Buch-/eBook-Cover für Traumatherapeutin
Zielgruppe
Ich bin Traumatherapeutin und schreibe ein Buch zum Thema Trauma bearbeiten.
Meine Zielgruppe sucht Heilung, Genesung, Selbstliebe etc.
Aufgabenstellung
Buchcover
Bitte erstell mir ein modernes positives inspirierendes Buchcover mit dem
Titel: 'Morgenlicht NEU entdecken“
Untertitel: „Spüre den Mut der ganz in dir wohnt“
Dr. Mira Kessow
Ich hätte gerne ein modernes Buch, das entweder einen Bezug zum Thema Trauma hat oder aber einfach stylische Schriftzüge. Bin aber auch offen für andere Vorschläge.
Dunkelblau, weiß und türkis oder auch rosa mag ich ganz gerne. Wobei Dunkelblau, weiß und türkis meine Favoriten sind und mit rosa höchstens kleinere Akzente gesetzt werden sollten.
Das Buchcover soll modern sein und direkt ansprechen. Gerne eine originelle Lösung, oder etwas Besonderes, etwas das Tiefe ausdrückt, oder man mehrmals hinsehen muss um etwas zu erkennen oder etwas das mehr Interpretationsspielraum lässt.
Gerne auch viel weiß, zumindest heller und nicht zu dunkel. Stylish, aber nicht überfrachtet.
Schreib mich gerne an, wenn du Fragen hast.
Ich habe mal zwei Beispiel von Typolösungen angehängt, die ich ganz cool fände.
Ich freue mich auf deine Ideen :-)
Ganz liebe Grüße
Mira

```html
<!DOCTYPE html>
<html lang="de">
<head>
<meta charset="utf-8">
<title>Morgenlicht NEU entdecken – Dr. Mira Kessow</title>
<link rel="stylesheet" href="https://fonts.googleapis.com/css2?family=Montserrat:wght@800&family=Parisienne&family=Source+Sans+3:wght@400&display=swap">
<style>
  :root {
    --sky: #b8d8e0;
    --cloud: #eef6f9;
    --turquoise: #58a2b8;
    --navy: #265a9e;
    --white: #ffffff;
    --blossom-light: #f6fafc;
    --blossom-mid: #dcedf5;
    --blossom-edge: #c4e2ef;
    --bud-pink: #ef9cc4;
  }
  html, body {
    margin: 0;
    padding: 0;
    overflow: hidden;
    background: var(--sky);
  }
  .cover {
    position: relative;
    width: 846px;
    height: 1200px;
    overflow: hidden;
    background:
      radial-gradient(ellipse 220px 170px at 720px 60px, rgba(238,246,249,0.75), rgba(238,246,249,0) 100%),
      radial-gradient(ellipse 260px 220px at 60px 1060px, rgba(238,246,249,0.8), rgba(238,246,249,0) 100%),
      radial-gradient(ellipse 320px 160px at 330px 1200px, rgba(238,246,249,0.7), rgba(238,246,249,0) 100%),
      var(--sky);
  }
  .blossom {
    position: absolute;
    left: 18px;
    top: 345px;
    width: 300px;
    height: 355px;
    border-radius: 46% 54% 42% 58% / 52% 44% 56% 48%;
    background: radial-gradient(ellipse at 52% 50%, var(--blossom-light) 0%, var(--blossom-mid) 55%, var(--blossom-edge) 100%);
    box-shadow: 0 0 18px rgba(255,255,255,0.6);
  }
  .author {
    position: absolute;
    top: 126px;
    left: 0;
    width: 846px;
    margin: 0;
    text-align: center;
    font-family: "Source Sans 3", sans-serif;
    font-weight: 400;
    font-size: 42px;
    letter-spacing: 0.5px;
    color: var(--white);
  }
  .title {
    margin: 0;
    font-weight: normal;
  }
  .title-line {
    position: absolute;
    left: 0;
    width: 846px;
    text-align: center;
    white-space: nowrap;
  }
  .title-top {
    top: 289px;
    font-family: "Montserrat", sans-serif;
    font-weight: 800;
    font-size: 88px;
    letter-spacing: -1px;
    line-height: 1;
    color: var(--turquoise);
  }
  .title-script {
    top: 352px;
    font-family: "Parisienne", cursive;
    font-size: 210px;
    line-height: 1;
    color: var(--navy);
  }
  .title-bottom {
    top: 572px;
    font-family: "Montserrat", sans-serif;
    font-weight: 800;
    font-size: 108px;
    line-height: 1;
    color: var(--turquoise);
  }
  .subtitle {
    position: absolute;
    left: 141px;
    top: 840px;
    width: 560px;
    margin: 0;
    font-family: "Source Sans 3", sans-serif;
    font-weight: 400;
    font-size: 44px;
    color: var(--navy);
  }
  .subtitle-first {
    display: block;
    height: 64px;
    line-height: 64px;
    white-space: nowrap;
  }
  .subtitle-accent {
    font-family: "Parisienne", cursive;
    font-size: 66px;
    margin-left: 6px;
  }
  .bud {
    display: inline-block;
    width: 18px;
    height: 22px;
    margin-left: 2px;
    vertical-align: 8px;
    border-radius: 50% 50% 45% 45%;
    background: radial-gradient(circle at 45% 40%, #fbe3ef 0%, var(--bud-pink) 70%);
  }
  .subtitle-second {
    display: block;
    text-align: right;
    line-height: 56px;
    white-space: nowrap;
  }
</style>
</head>
<body>
<main class="cover">
  <div class="blossom" role="img" aria-label="Illustration: zarte weiß-hellblaue Blüte, halb hinter dem Titel"></div>

  <p class="author">DR. MIRA KESSOW</p>

  <h1 class="title">
    <span class="title-line title-top">MORGENLICHT</span>
    <span class="title-line title-script">neu</span>
    <span class="title-line title-bottom">ENTDECKEN</span>
  </h1>

  <p class="subtitle">
    <span class="subtitle-first">Spüre den<span class="subtitle-accent">Mut</span><span class="bud" role="img" aria-label="Illustration: kleine rosa Knospe"></span></span>
    <span class="subtitle-second">der ganz in dir wohnt!</span>
  </p>
</main>
</body>
</html>
```